Looking for business card/letterhead/email signature

Take existing logo and create full design suite of collateral

Contact Information for Business Card

Use mock details that can be edited by us

Font styles to use
Sans Serif

```html
<!DOCTYPE html>
<html lang="en">
<head>
<meta charset="utf-8">
<title>Harlow Digital – Stationery Suite</title>
<link href="https://fonts.googleapis.com/css2?family=Roboto:wght@400;500;700&family=Roboto+Condensed:wght@400;700&family=Questrial&display=swap" rel="stylesheet">
<style>
  :root{
    --bg:#dcdcdc;
    --paper:#ffffff;
    --brand:#0a4b91;
    --brand-deep:#034e93;
    --ink:#3a3a3a;
    --ink-soft:#666666;
    --rule:#8a8a8a;
    --divider:#b9b9b9;
    --sig-tint:#dfe6f2;
  }
  *{box-sizing:border-box;margin:0;padding:0}
  html,body{width:1200px;height:738px;overflow:hidden;background:var(--bg)}
  body{position:relative;font-family:"Roboto",Arial,sans-serif;color:var(--ink)}
  .sheet{position:absolute;background:var(--paper);box-shadow:0 1px 4px rgba(0,0,0,.18)}

  /* brand lockup */
  .brand{position:absolute;display:flex;align-items:center;gap:.3em;color:var(--brand);
    font-family:"Roboto",Arial,sans-serif;font-weight:700;white-space:nowrap;line-height:1;letter-spacing:-.01em}
  .brand__dot{width:.55em;height:.55em;border-radius:50%;background:currentColor;flex:none}
  .brand--light{color:#ffffff}

  /* letterhead */
  .letterhead{left:66px;top:107px;width:452px;height:583px}
  .letterhead .brand{left:50%;top:50px;transform:translateX(-50%);font-size:20px}
  .letter__salutation{position:absolute;left:41px;top:170px;font-family:"Questrial",sans-serif;font-size:11.5px;color:#444}
  .letter__body{position:absolute;left:41px;top:202px;width:374px;font-family:"Questrial",sans-serif;font-size:6.6px;line-height:9.6px;color:var(--ink-soft);text-align:justify}
  .letter__body p{margin-bottom:9.6px}
  .letter__closing{position:absolute;left:41px;top:407px;font-family:"Questrial",sans-serif;font-size:6.6px;color:var(--ink-soft)}
  .letter__signature{position:absolute;left:38px;top:436px;width:82px;height:34px;border-radius:4px;background:linear-gradient(90deg,var(--sig-tint),#eef2f8)}
  .letter__footer{position:absolute;left:0;right:0;top:545px;text-align:center;font-size:5.6px;color:var(--ink)}
  .letter__footer .rule{width:252px;height:1px;background:var(--rule);margin:3px auto 4px}
  .letter__footer b{font-weight:500}

  /* email signature */
  .signature{left:582px;top:107px;width:522px;height:79px}
  .signature .brand{left:22px;top:33px;font-size:12px}
  .signature__divider{position:absolute;top:18px;height:45px;width:1px;background:var(--divider)}
  .signature__person{position:absolute;left:172px;top:30px;font-family:"Roboto Condensed",sans-serif;color:var(--brand)}
  .signature__person .name{font-size:11px;font-weight:700;line-height:1.1}
  .signature__person .role{font-size:7.5px;font-weight:700;color:#333;margin-top:1px}
  .signature__company{position:absolute;left:266px;top:27px;font-size:6.8px;line-height:9.4px;color:#333}
  .signature__contacts{position:absolute;left:404px;top:21px;list-style:none;font-size:6.8px;line-height:9.7px;color:#333}
  .signature__contacts li{display:flex;align-items:center;gap:4px}
  .signature__contacts svg{width:7px;height:7px;fill:var(--brand);flex:none}

  /* business card */
  .card{top:203px;width:250px;height:143px}
  .card--front{left:578px}
  .card--front .brand{left:50%;top:42px;transform:translateX(-50%);font-size:16px}
  .card__name{position:absolute;left:0;right:0;top:84px;line-height:11px;text-align:center;font-family:"Roboto Condensed",sans-serif;color:var(--brand)}
  .card__name .name{font-size:9px;font-weight:700}
  .card__name .role{font-size:6.3px;color:#333}
  .card__rule{position:absolute;left:38px;right:38px;top:98px;height:1px;background:linear-gradient(90deg,transparent,#cfcfcf,transparent)}
  .card__details{position:absolute;left:0;right:0;top:102px;text-align:center;font-size:5.8px;line-height:8.6px;color:#333}
  .card__web{letter-spacing:.18em}
  .card--back{left:850px;background:var(--brand-deep)}
  .card--back .brand{left:50%;top:64px;transform:translateX(-50%);font-size:18px}

  /* envelope */
  .envelope-back{left:576px;top:362px;width:530px;height:231px;box-shadow:none;background:transparent}
  .envelope-back__body{position:absolute;left:0;top:0;width:530px;height:231px;background:var(--paper);box-shadow:0 1px 4px rgba(0,0,0,.16)}
  .envelope-back svg.flap{position:absolute;left:0;top:0}
  .envelope-back .brand{left:50%;top:33px;transform:translateX(-50%);font-size:12px}
  .envelope-front{left:549px;top:458px;width:530px;height:231px}
  .envelope-front .brand{left:26px;top:46px;font-size:16px}
  .envelope-front__rule{position:absolute;left:26px;right:0;top:204px;height:1px;background:var(--rule)}
  .envelope-front__address{position:absolute;left:26px;top:211px;font-size:5.8px;color:#333}
  .envelope-front__address b{font-weight:500}
</style>
</head>
<body>

  <section class="sheet letterhead">
    <div class="brand"><span class="brand__dot"></span>Harlow Digital</div>
    <p class="letter__salutation">Dear Mr. Reyes,</p>
    <div class="letter__body">
      <p>Thank you for meeting with our team last week. We have prepared an outline of the proposed work, covering strategy, design and a schedule for each phase. Our goal is to keep the process simple, clear and focused on results that matter to your business, with regular check-ins along the way.</p>
      <p>The first phase begins with a short discovery session, where we review your current materials and agree on priorities. From there we will draft initial concepts and share them for feedback before moving into refinement and final delivery of all files.</p>
      <p>Each stage includes time for revisions, so you can be confident the finished work reflects your brand. We will provide print-ready artwork for cards, letterheads and envelopes, along with digital versions for email and web use. Pricing and timelines are attached for your review, and we are happy to adjust them to suit your needs.</p>
      <p>Please let us know a convenient time to talk through the details. We look forward to working with you and building something great together.</p>
    </div>
    <p class="letter__closing">Sincerely,</p>
    <div class="letter__signature" role="img" aria-label="Handwritten signature of Daniel Reyes"></div>
    <div class="letter__footer">
      <div><b>Harlow Digital</b> 214 Cedar Hollow Road, Bellmont, Oregon 97512</div>
      <div class="rule"></div>
      <div><b>Ph :</b> 555 210 4836 <b>E-mail :</b> hello@harlowdigital.com <b>Web :</b> www.harlowdigital.com</div>
    </div>
  </section>

  <section class="sheet signature">
    <div class="brand"><span class="brand__dot"></span>Harlow Digital</div>
    <span class="signature__divider" style="left:141px"></span>
    <div class="signature__person">
      <div class="name">DANIEL REYES</div>
      <div class="role">CEO/FOUNDER</div>
    </div>
    <span class="signature__divider" style="left:249px"></span>
    <div class="signature__company">
      <div>Harlow Digital</div>
      <div>214 Cedar Hollow Road</div>
      <div>Bellmont, Oregon 97512</div>
    </div>
    <span class="signature__divider" style="left:375px"></span>
    <ul class="signature__contacts">
      <li><svg viewBox="0 0 10 10"><path d="M2 0.5l2 2-1 1.3c.6 1.3 1.6 2.3 2.9 2.9L7.2 5.7l2.3 2-1.2 1.9C4.5 9.3.7 5.5.4 1.7z"/></svg>555 210 4836</li>
      <li><svg viewBox="0 0 10 10"><path d="M3 0h4a1 1 0 0 1 1 1v8a1 1 0 0 1-1 1H3a1 1 0 0 1-1-1V1a1 1 0 0 1 1-1zm0 1.2v6.4h4V1.2z"/></svg>555 318 7702</li>
      <li><svg viewBox="0 0 10 10"><path d="M0 2h10v1L5 6 0 3zM0 4.2l5 3 5-3V8H0z"/></svg>daniel@harlowdigital.com</li>
      <li><svg viewBox="0 0 10 10"><circle cx="5" cy="5" r="4.6"/><path d="M1 5h8M5 .6v8.8" stroke="#fff" stroke-width=".8" fill="none"/></svg>www.harlowdigital.com</li>
    </ul>
  </section>

  <section class="sheet card card--front">
    <div class="brand"><span class="brand__dot"></span>Harlow Digital</div>
    <div class="card__name"><span class="name">Daniel Reyes</span> <span class="role">- CEO/Founder</span></div>
    <div class="card__rule"></div>
    <div class="card__details">
      <div>214 Cedar Hollow Road, Bellmont, Oregon 97512</div>
      <div>P. 555 210 4836 M . 555 318 7702 E . daniel@harlowdigital.com</div>
      <div class="card__web">www.harlowdigital.com</div>
    </div>
  </section>
  <section class="sheet card card--back">
    <div class="brand brand--light"><span class="brand__dot"></span>Harlow Digital</div>
  </section>

  <section class="sheet envelope-back">
    <div class="envelope-back__body"></div>
    <svg class="flap" width="530" height="80" viewBox="0 0 530 80" aria-hidden="true">
      <path d="M0 0H530L514 66Q511 76 500 76H30Q19 76 16 66Z" fill="var(--brand-deep)"/>
    </svg>
    <div class="brand brand--light"><span class="brand__dot"></span>Harlow Digital</div>
  </section>
  <section class="sheet envelope-front">
    <div class="brand"><span class="brand__dot"></span>Harlow Digital</div>
    <div class="envelope-front__rule"></div>
    <div class="envelope-front__address"><b>Harlow Digital</b> 214 Cedar Hollow Road, Bellmont, Oregon 97512</div>
  </section>

</body>
</html>
```